Business Card Design Project

We are a construction company in Orange County, CA. We need a two sided business card. We would like the back to be our logo with web URL. Front should included Name, title, address, phone, fax and email address.

our address is
627 West Dorrance Blvd, Suite 308
Anaheim, CA 92718

Our logo files are attached.

Construction

```html
<!DOCTYPE html>
<html lang="en">
<head>
<meta charset="utf-8">
<title>Halvor Business Card</title>
<link href="https://fonts.googleapis.com/css2?family=Source+Sans+3:wght@400;600;700&display=swap" rel="stylesheet">
<style>
  :root {
    --brand-blue: #1b4a7c;
    --ink-grey: #555a60;
    --card-white: #ffffff;
    --backdrop: #e9e7e4;
  }
  * { box-sizing: border-box; margin: 0; padding: 0; }
  html, body { width: 1200px; height: 444px; overflow: hidden; }
  body {
    background: var(--backdrop);
    font-family: "Source Sans 3", "Helvetica Neue", Arial, sans-serif;
    position: relative;
  }
  .card {
    position: absolute;
    width: 516px;
    height: 294px;
    background: var(--card-white);
    border-radius: 14px;
    box-shadow: 0 3px 8px rgba(0,0,0,0.18);
    overflow: hidden;
  }
  .card--front { left: 67px; top: 72px; }
  .card--back { left: 617px; top: 78px; }

  .identity {
    position: absolute;
    top: 42px; left: 0; right: 0;
    text-align: center;
    font-size: 16px;
    color: var(--brand-blue);
  }
  .identity__name { font-weight: 700; letter-spacing: 0.2px; }
  .identity__divider {
    display: inline-block;
    width: 1px; height: 22px;
    background: #8a8f96;
    vertical-align: -5px;
    margin: 0 6px 0 7px;
  }
  .identity__title { font-weight: 400; color: var(--ink-grey); font-size: 14px; }

  .brand-band {
    position: absolute;
    top: 98px; left: 0; right: 0;
    height: 62px;
    display: flex;
  }
  .brand-band__bar { flex: 1; background: var(--brand-blue); }
  .brand-band__gap {
    width: 260px;
    display: flex;
    align-items: center;
    justify-content: center;
  }
  .wordmark {
    font-weight: 700;
    color: var(--brand-blue);
    font-size: 58px;
    line-height: 1;
    letter-spacing: -1px;
  }

  .contact-row {
    position: absolute;
    top: 216px; left: 0; right: 0;
    display: flex;
    justify-content: center;
    gap: 12px;
    font-size: 13.5px;
    color: var(--ink-grey);
  }
  .contact-row__item { display: flex; align-items: center; gap: 3px; white-space: nowrap; }
  .contact-row__item svg { width: 11px; height: 11px; fill: var(--brand-blue); }
  .address {
    position: absolute;
    top: 245px; left: 0; right: 0;
    text-align: center;
    font-size: 13.5px;
    color: var(--ink-grey);
  }

  .back-brand {
    position: absolute;
    top: 110px; left: 0; right: 0;
    text-align: center;
  }
  .back-brand .wordmark { font-size: 66px; }
  .back-url {
    position: absolute;
    top: 198px; left: 0; right: 0;
    text-align: center;
    font-size: 14.5px;
    letter-spacing: 2.4px;
    color: var(--brand-blue);
  }
</style>
</head>
<body>
  <section class="card card--front" aria-label="Card front">
    <p class="identity">
      <span class="identity__name">YOUR NAME</span><span class="identity__divider"></span><span class="identity__title">Title</span>
    </p>

    <div class="brand-band">
      <div class="brand-band__bar"></div>
      <div class="brand-band__gap"><span class="wordmark">HALVOR</span></div>
      <div class="brand-band__bar"></div>
    </div>

    <div class="contact-row">
      <span class="contact-row__item">
        <svg viewBox="0 0 12 12" aria-hidden="true"><path d="M2.5 0.8l2 2.2-1 1.3c.6 1.5 1.8 2.7 3.3 3.3l1.3-1 2.2 2-1 1.9C5 10.3 1.7 7 0.6 1.8z"/></svg>
        0714263580
      </span>
      <span class="contact-row__item">
        <svg viewBox="0 0 12 12" aria-hidden="true"><rect x="3" y="1" width="6" height="3"/><rect x="0.5" y="4.5" width="11" height="4.5" rx="1"/><rect x="3" y="8" width="6" height="3"/></svg>
        0714263581
      </span>
      <span class="contact-row__item">
        <svg viewBox="0 0 12 12" aria-hidden="true"><path d="M0.5 2.5h11v7h-11z M1 3l5 3.5 5-3.5" stroke="#fff" stroke-width="0.8"/></svg>
        info@halvorbuild.com
      </span>
      <span class="contact-row__item">
        <svg viewBox="0 0 12 12" aria-hidden="true"><circle cx="6" cy="6" r="5.5"/><path d="M0.5 6h11M6 0.5v11M6 0.5c-3 3-3 8 0 11M6 0.5c3 3 3 8 0 11" stroke="#fff" stroke-width="0.7" fill="none"/></svg>
        www.halvorbuild.com
      </span>
    </div>
    <p class="address">627 West Dorrance Blvd, Suite 308 Anaheim, CA 92718</p>
  </section>

  <section class="card card--back" aria-label="Card back">
    <div class="back-brand"><span class="wordmark">HALVOR</span></div>
    <p class="back-url">www.halvorbuild.com</p>
  </section>
</body>
</html>
```